Healthcare website

We want to replace our website using joomla as the CMS. We want it to be device agnostic (gantry etc). Our business is health care our clients are people with high level spinal cord injuries ( quadriplegia / tetraplegia etc ). The site is a marketing tool primarily to potential clients and a portal for existing staff to access forms etc. It will showcase our key staff and our capability. It will also be where any new recruits apply to work with us. It must allow us to integrate our social media initiatives also. The final design must convey sophistication, high quality care and be warm and welcoming.

current web site is www.tendralwick.com.au
Updates

I have made small change to the brief in that i have removed the prefered color and indicated it would be nice to see some images that symbolize change / transformation like butterflies etc. thank you

Target Market(s)

Our business is health care our clients are people with high level spinal cord injuries ( quadriplegia / tetraplegia etc ).

Industry/Entity Type

Marketing

Colors

Designer to choose colors to be used in the design.

Requirements
Must have
• The site is a marketing tool primarily to potential clients and a portal for existing staff to access forms etc. It will showcase our key staff and our capability. It will also be where any new recruits apply to work with us. It must allow us to integrate our social media initiatives also. The final design must convey sophistication, high quality care and be warm and welcoming.
Nice to have
• Would be nice to incorporate images that symbolize change and new transformations - butterflies etc.

```html
<!DOCTYPE html>
<html lang="en">
<head>
<meta charset="utf-8">
<title>Tendralwick Care – Home</title>
<link href="https://fonts.googleapis.com/css2?family=Roboto+Condensed:wght@400;700&family=Roboto:wght@400;500&display=swap" rel="stylesheet">
<style>
:root{
  --blue:#1f6cc4;
  --blue-dark:#15559e;
  --topline:#1e5fd8;
  --text:#555a60;
  --text-light:#777c82;
  --rule:#dcdcdc;
  --btn-grey:#5c6066;
  --footer:#333436;
  --footer-deep:#262729;
  --footer-text:#a5a8ab;
  --white:#ffffff;
  --card-border:#f0c8d0;
}
*{box-sizing:border-box;margin:0;padding:0}
html,body{width:1200px;height:2727px;overflow:hidden}
body{position:relative;background:var(--white);font-family:"Roboto",Arial,sans-serif;color:var(--text)}
h1,h2,h3{font-weight:400}
.abs{position:absolute}

.topline{left:0;top:0;width:1200px;height:4px;background:var(--topline)}
.brand{left:133px;top:42px;display:flex;align-items:center;gap:8px;font-family:"Roboto Condensed",sans-serif;font-size:26px;color:var(--blue);font-weight:700}
.brand-dot{width:28px;height:28px;border-radius:50%;background:var(--blue)}
.nav{right:131px;top:50px;display:flex;gap:56px;font-family:"Roboto Condensed",sans-serif;font-size:17px;font-weight:700;color:#333}
.nav .active{color:var(--blue)}

.hero{left:133px;top:105px;width:936px;height:491px;border:1px solid #ddd;
  background:linear-gradient(100deg,#e4e9ee 0%,#dfe5ec 30%,#c9d7e6 55%,#b9cde2 75%,#d7e1ec 100%)}
.hero-brand{left:614px;top:288px;display:flex;align-items:center;gap:10px;font-family:"Roboto Condensed",sans-serif;font-size:40px;font-weight:700;color:var(--blue)}
.hero-brand .dot{width:44px;height:44px;border-radius:50%;background:var(--blue)}
.hero-text{left:614px;top:372px;width:390px;font-size:16px;line-height:30px;color:var(--blue)}
.hero-arrows{left:1002px;top:555px;display:flex;gap:4px}
.hero-arrows span{width:24px;height:23px;background:#4a4d52;display:flex;align-items:center;justify-content:center}

.join-title{left:150px;top:626px;font-size:15px;color:var(--blue);font-weight:500}
.join-sub{left:150px;top:663px;font-size:12.5px;color:var(--text)}
.join-btn{left:844px;top:625px;width:206px;height:46px;border-radius:23px;background:linear-gradient(#3d8fe0,#1b5fb5);color:#fff;font-family:"Roboto Condensed",sans-serif;font-size:18px;font-weight:700;display:flex;align-items:center;justify-content:center}
.rule{height:1px;background:var(--rule)}

.section-title{font-family:"Roboto Condensed",sans-serif;font-weight:700;font-size:21px;color:var(--blue)}
.services-title{left:0;width:1200px;top:736px;text-align:center}
.services-intro{left:200px;width:800px;top:776px;text-align:center;font-size:10.5px;line-height:22px;color:var(--text)}

.card{width:294px;height:193px;top:847px;border:1px solid var(--card-border);padding:8px}
.card-img{width:100%;height:100%}
.card-title{top:1054px;font-family:"Roboto Condensed",sans-serif;font-size:16px;color:var(--blue)}
.ticks{top:1092px;width:290px;list-style:none;font-size:10.5px;line-height:19px;color:var(--text)}
.ticks li{position:relative;padding-left:24px;margin-bottom:8px}
.ticks li svg{position:absolute;left:0;top:4px}
.card-para{top:1092px;width:290px;font-size:10.5px;line-height:19px;color:var(--text)}
.read-more{top:1232px;font-size:12px;color:var(--blue)}

.welcome-img{left:133px;top:1338px;width:294px;height:198px;background:linear-gradient(135deg,#3a4a3c,#6c7a5e 45%,#c9c9c4 70%,#2b3036)}
.welcome-text{left:458px;top:1336px;width:612px;font-size:10.5px;line-height:27px;color:var(--text)}
.grey-btn{background:linear-gradient(#6d7177,#4f5358);color:#fff;font-family:"Roboto Condensed",sans-serif;font-size:14px;display:flex;align-items:center;justify-content:center;border-radius:2px}

.team-arrows{left:562px;top:1597px;font-size:16px;color:#aaa;letter-spacing:12px}
.member-photo{left:133px;width:82px;height:82px;border:1px solid #ddd}
.member-name{left:238px;font-family:"Roboto Condensed",sans-serif;font-size:15px;color:var(--blue)}
.member-bio{left:238px;width:362px;font-size:10.5px;line-height:22px;color:var(--text)}

.news-intro{left:631px;top:1630px;width:440px;font-size:10.5px;line-height:22px;color:var(--text)}
.news-sub{left:633px;top:1707px;font-family:"Roboto Condensed",sans-serif;font-size:15px;color:var(--blue)}
.news-list{left:631px;top:1743px;width:440px}
.news-list li{margin-bottom:16px}

.social-band{left:133px;top:1991px;width:936px;height:327px;background:linear-gradient(90deg,#d5d2cc,#c3c7c9 30%,#cfc9c0 60%,#c2c6cc)}
.social-box{left:215px;top:2047px;width:774px;height:204px;background:#fff;box-shadow:0 0 6px rgba(0,0,0,.15)}
.social-title{left:254px;top:2077px;font-family:"Roboto Condensed",sans-serif;font-weight:700;font-size:30px;color:var(--blue)}
.social-sub{left:256px;top:2127px;font-family:"Roboto Condensed",sans-serif;font-size:17px;color:#333}
.social-copy{left:256px;top:2162px;width:300px;font-size:10.5px;line-height:22px;color:var(--text)}
.connect-bar{left:600px;top:2116px;width:362px;height:64px;background:#3b5998;display:flex;align-items:center;padding-left:22px;gap:24px;color:#fff}
.connect-bar .name{font-family:"Roboto Condensed",sans-serif;font-size:30px;font-weight:700}
.connect-bar .cta{font-size:12px}

.footer{left:0;top:2318px;width:1200px;height:355px;background:var(--footer)}
.footer-title{font-family:"Roboto Condensed",sans-serif;font-size:20px;color:#c8cacc}
.footer-text{font-size:10.5px;line-height:20px;color:var(--footer-text)}
.footer-list{list-style:none}
.footer-list li{position:relative;padding-left:20px;margin-bottom:14px}
.footer-list li::before{content:"";position:absolute;left:2px;top:8px;width:5px;height:5px;border-radius:50%;background:var(--footer-text)}
.map{left:755px;top:2363px;width:245px;height:202px;background:linear-gradient(135deg,#e8e3d2,#d9dcc4 50%,#e6d9b8)}
.footer-rule{left:133px;top:2587px;width:936px;height:1px;background:#4a4b4e}
.social-icons{left:148px;top:2614px;display:flex;gap:10px}
.social-icons span{width:27px;height:27px;border-radius:3px}
.newsletter-label{left:400px;top:2612px;font-family:"Roboto Condensed",sans-serif;font-size:22px;color:#c8cacc}
.newsletter-copy{left:524px;top:2609px;width:260px;padding-left:12px;border-left:1px solid #555;font-size:9.5px;line-height:18px;color:var(--footer-text)}
.email{left:798px;top:2612px;width:249px;height:37px;background:#eceded;display:flex;align-items:center;padding-left:12px;gap:10px;font-size:10px;color:#999}
.copyright{left:0;top:2673px;width:1200px;height:54px;background:var(--footer-deep);color:#8d9094;font-size:11px;display:flex;align-items:center;justify-content:center}
</style>
</head>
<body>

<div class="abs topline"></div>
<div class="abs brand"><span class="brand-dot"></span>Tendralwick Care</div>
<nav class="abs nav">
  <span class="active">HOME</span><span>ABOUT US</span><span>OUR SERVICES</span><span>RESOURCES</span><span>CONTACT US</span>
</nav>

<div class="abs hero" role="img" aria-label="Photo of a smiling doctor with a stethoscope in a bright clinic, colleagues in the background"></div>
<div class="abs hero-brand"><span class="dot"></span>Tendralwick Care</div>
<p class="abs hero-text">TBA is a Division 1 Registered Nurse and comes to Tendralwick Care with a strong passion for caring for people. Having previously worked for the....</p>
<div class="abs hero-arrows">
  <span><svg width="10" height="12" viewBox="0 0 10 12"><path d="M7 1 2 6l5 5" stroke="#fff" stroke-width="2" fill="none"/></svg></span>
  <span><svg width="10" height="12" viewBox="0 0 10 12"><path d="M3 1l5 5-5 5" stroke="#fff" stroke-width="2" fill="none"/></svg></span>
</div>

<p class="abs join-title">Tendralwick Care We are always on the lookout for great people to work with our clients</p>
<p class="abs join-sub">As Founder of Tendralwick Care, I am reminded daily of the extraordinary dedication, and level of compassion our team</p>
<div class="abs join-btn">JOIN OUR TEAM</div>
<div class="abs rule" style="left:133px;top:700px;width:936px"></div>

<h2 class="abs section-title services-title">OUR SERVICES</h2>
<p class="abs services-intro">Passionate and committed to making a difference Marla Ventrice has a reputation of professionalism, integrity and success. With over 20 years Passionate and committed to Marla Ventrice has a reputation of professionalism, integrity and success. With over 20 years......</p>

<div class="abs card" style="left:133px"><div class="card-img" role="img" aria-label="Photo of a carer helping a man beside a car" style="background:linear-gradient(135deg,#b9b2a8,#7a5a4e 50%,#3a3a3e)"></div></div>
<div class="abs card" style="left:453px"><div class="card-img" role="img" aria-label="Photo of a smiling woman in a wheelchair" style="background:linear-gradient(135deg,#d8d6cf,#e8c4c9 50%,#3b3536)"></div></div>
<div class="abs card" style="left:773px"><div class="card-img" role="img" aria-label="Photo of a carer and a smiling boy" style="background:linear-gradient(135deg,#d9c9b0,#2f3d5e 55%,#d8d4cc)"></div></div>

<h3 class="abs card-title" style="left:133px">ATTENDANT CARE - PERSONAL CARE</h3>
<h3 class="abs card-title" style="left:453px">SPINAL CARE - SCI</h3>
<h3 class="abs card-title" style="left:773px">REFER A CLIENT</h3>

<ul class="abs ticks" style="left:133px">
  <li><svg width="12" height="10" viewBox="0 0 12 10"><path d="M1 5l3.5 3.5L11 1" stroke="#1f6cc4" stroke-width="1.6" fill="none"/></svg>Tendralwick Care has built its services around the needs of each and every client......</li>
  <li><svg width="12" height="10" viewBox="0 0 12 10"><path d="M1 5l3.5 3.5L11 1" stroke="#1f6cc4" stroke-width="1.6" fill="none"/></svg>Guarantee that your carers will always be there for you.</li>
  <li><svg width="12" height="10" viewBox="0 0 12 10"><path d="M1 5l3.5 3.5L11 1" stroke="#1f6cc4" stroke-width="1.6" fill="none"/></svg>Professionally support one-to-one home-based care for people with disabilities.</li>
</ul>
<ul class="abs ticks" style="left:453px">
  <li><svg width="12" height="10" viewBox="0 0 12 10"><path d="M1 5l3.5 3.5L11 1" stroke="#1f6cc4" stroke-width="1.6" fill="none"/></svg>Our Care Managers are Registered Division 1 Nurses with extensive experience in SCI</li>
  <li><svg width="12" height="10" viewBox="0 0 12 10"><path d="M1 5l3.5 3.5L11 1" stroke="#1f6cc4" stroke-width="1.6" fill="none"/></svg>We continually review our service delivery best practice</li>
  <li><svg width="12" height="10" viewBox="0 0 12 10"><path d="M1 5l3.5 3.5L11 1" stroke="#1f6cc4" stroke-width="1.6" fill="none"/></svg>We listen to and support our Care Team members and Clients - feedback is paramount</li>
</ul>
<p class="abs card-para" style="left:773px">At Tendralwick Care our clients care is our 1st priority. Our measure of success is their satisfaction. We provide thousands of hours of care per month and we proudly have a 100% service delivery record! At Tendralwick Care we guarantee our care: our service delivery record.....</p>

<span class="abs read-more" style="left:143px">[ READ MORE + ]</span>
<span class="abs read-more" style="left:463px">[ READ MORE + ]</span>
<span class="abs read-more" style="left:783px">[ READ MORE + ]</span>

<div class="abs rule" style="left:133px;top:1273px;width:936px"></div>

<h2 class="abs section-title" style="left:133px;top:1294px">WELCOME TO TENDRALWICK CARE</h2>
<div class="abs welcome-img" role="img" aria-label="Photo of three smiling men together outdoors"></div>
<p class="abs welcome-text">Tendralwick Care is a small team of care professionals committed to providing quality one-to-one care with heart Tendralwick Care has built its service around the needs of each and every client. We listen to and consult with our clients, their families, Care Teams and the wider care community Tendralwick Care is a privately owned organisation providing in home care for people with disabilities (attendant care) throughout the State of Victoria. We commenced operation on the 1st of July 2004 at our principal Victoria. We are committed to our Vision - "to provide the BEST care....................</p>
<div class="abs grey-btn" style="left:456px;top:1494px;width:204px;height:42px">CLICK HERE FOR MORE INFO</div>

<h2 class="abs section-title" style="left:133px;top:1594px">OUR TEAMS</h2>
<div class="abs team-arrows">‹ ›</div>

<div class="abs member-photo" style="top:1633px;background:linear-gradient(135deg,#e6dcd4,#b8743c 50%,#ead8c8)" role="img" aria-label="Portrait of Marla Ventrice"></div>
<h3 class="abs member-name" style="top:1638px">MARLA VENTRICE</h3>
<p class="abs member-bio" style="top:1666px">Passionate and committed to making a difference Marla Ventrice has a reputation of professionalism, integrity and success. With over 20 years...</p>

<div class="abs member-photo" style="top:1745px;background:linear-gradient(135deg,#e4e4e4,#6a6a6e 50%,#d4d4d8)" role="img" aria-label="Portrait of Dale Orvington"></div>
<h3 class="abs member-name" style="top:1750px">DALE ORVINGTON</h3>
<p class="abs member-bio" style="top:1778px">Passionate and committed to making a difference Marla Ventrice has a reputation of professionalism, integrity and success. With over 20 years...</p>

<div class="abs member-photo" style="top:1856px;background:linear-gradient(135deg,#eee,#3a2a24 50%,#2e4a80)" role="img" aria-label="Portrait of Nina Carrowby"></div>
<h3 class="abs member-name" style="top:1861px">NINA CARROWBY</h3>
<p class="abs member-bio" style="top:1889px">Passionate and committed to making a difference Marla Ventrice has a reputation of professionalism, integrity and success. With over 20 years...</p>

<h2 class="abs section-title" style="left:631px;top:1594px">DISABILITY NEWS</h2>
<p class="abs news-intro">The latest Spinal Cord Injury News, Information and Resources for People living with SCI Spinal Cord Injury The latest Spinal Cord Injury News, Information and Resources for People living with SCI Spinal Cord Injury........</p>
<h3 class="abs news-sub">Spinal Cord Injury Zone</h3>
<ul class="abs ticks news-list">
  <li><svg width="12" height="10" viewBox="0 0 12 10"><path d="M1 5l3.5 3.5L11 1" stroke="#1f6cc4" stroke-width="1.6" fill="none"/></svg>New Methods Show Promise for Rehabilitating Paralyzed Patients With Spinal Cord Injury.......</li>
  <li><svg width="12" height="10" viewBox="0 0 12 10"><path d="M1 5l3.5 3.5L11 1" stroke="#1f6cc4" stroke-width="1.6" fill="none"/></svg>Stem-cell advances may quell ethics debate</li>
  <li><svg width="12" height="10" viewBox="0 0 12 10"><path d="M1 5l3.5 3.5L11 1" stroke="#1f6cc4" stroke-width="1.6" fill="none"/></svg>Wheelchair rugby a family affair for mom and son</li>
  <li><svg width="12" height="10" viewBox="0 0 12 10"><path d="M1 5l3.5 3.5L11 1" stroke="#1f6cc4" stroke-width="1.6" fill="none"/></svg>Attitude can play significant role in recovery from paralyzing injury</li>
</ul>
<div class="abs grey-btn" style="left:634px;top:1914px;width:144px;height:42px">READ MORE</div>

<div class="abs social-band" role="img" aria-label="Faded photo mosaic of smiling people of all ages"></div>
<div class="abs social-box"></div>
<h2 class="abs social-title">TENDRALWICK CARE</h2>
<p class="abs social-sub">Connect with Social Network</p>
<p class="abs social-copy">Duis aute irure dolor in reprehenderit in voluptate velit esse cillum. Dolore magna aliqua. Ut enim....</p>
<div class="abs connect-bar"><span class="name">Linkspace</span><span class="cta">Connect With Linkspace</span></div>

<div class="abs footer"></div>
<h3 class="abs footer-title" style="left:140px;top:2345px">About Us</h3>
<p class="abs footer-text" style="left:140px;top:2390px;width:230px">Lorem ipsum dolor sit amet, consectetur adipi scing elit. Vestibulum iaculis massa nec velit commodo lobortis.Quisque diam lacus, tincidunt vitae eros porta, sagittis rhoncus est. Quisque sed justo commodo lobortis.Quisque diam lacus, tincidunt vitae eros porta, sagittis rhoncus est. Quisque sed justo............</p>

<h3 class="abs footer-title" style="left:473px;top:2345px">Store Location</h3>
<p class="abs footer-text" style="left:473px;top:2390px">Feel free to contact us if you have any problems.</p>
<ul class="abs footer-text footer-list" style="left:473px;top:2430px;width:240px">
  <li>Address :Tendralwick Care - Melbourne 42 - 44 Ardley Grove Rd Kelsbrook Victoria, 3187</li>
  <li>Email : info@tendralwick.com.au</li>
  <li>Phone : (03) 9000 4172</li>
</ul>
<div class="abs map" role="img" aria-label="Street map showing the office location with markers"></div>

<div class="abs footer-rule"></div>
<div class="abs social-icons">
  <span style="background:#3b5998"></span><span style="background:#2fa9e0"></span><span style="background:#f39220"></span><span style="background:#d92c27"></span><span style="background:#3cb4d8"></span>
</div>
<div class="abs newsletter-label">NewsLetter :</div>
<p class="abs newsletter-copy">In venenatis neque a eros laoreet eu placerat erat suscipit. Fusce cursus, erat ut scelerisque condimentum</p>
<div class="abs email">
  <svg width="16" height="11" viewBox="0 0 16 11"><rect x=".5" y=".5" width="15" height="10" fill="#bbb" stroke="#999"/><path d="M1 1l7 5 7-5" stroke="#888" fill="none"/></svg>
  <span>Enter Your Email Address</span>
  <svg style="margin-left:auto;margin-right:12px" width="8" height="12" viewBox="0 0 8 12"><path d="M1 1l5 5-5 5" stroke="#aaa" stroke-width="1.5" fill="none"/></svg>
</div>

<div class="abs copyright">© Copy Rights 2014 Tendralwick Care.All Rights Reserved.</div>

</body>
</html>
```